Plakat-Design für kleine deutsche Immobilien- und Reiseveranstalter-Firma
Zielgruppe
Kleine deutsche Immobilien- und Reiseveranstalter-Firma, spezialisiert auf Italien. In Italien sind es Immobilienbesitzer, die aus versch. Gründen hoffen an Ausländer zu verkaufen/vermieten ( Alter ca. ab 35-40)
Aufgabenstellung
Um neue Immo-Besitzer anzusprechen, lassen wir in verschiedenen Gemeinden in der Nordtoskana Plakate gegen Gebühr kleben ( 70 x 100, meistens 1 bis 2 Wochen)
Text auf Italienisch
Was an Text rein muss( falls Sie es anders mitteilen wollen, bin ich gerne bereit es zu diskutieren)
VUOI VENDERE CASA A STRANIERI O AFFITTARLA A TURISTI ? (Übersetzung ca.:= wollen Sie Ihre Immobilie an Ausländer verkaufen oder an Touristen vermieten?)
Verdona
Germania – info@verdona-beispiel.de + 49 7412 3810457
Italia – 0571 – 394062, Cell.: 371 – 2094716, 335- 47 92608,
www.verdonacase-beispiel.com
www.verdonaaffitti-beispiel.com
Der Poster, den man meistens im Vorbeifahren sieht, soll springt sofort ins Auge , fast aufdringlich. Man kann mit Farben oder Bildern (oder beiden) arbeiten. Stechende Farben, sonst minimalistisch einfach. (??)
Erfahrung zeigt, daß die beiden Mobile Nummern (Cell.:) mehr sichtbar sein könnten. Ich kann zwei letzte zeigen, aber ungern, weil sie mir nicht gefallen und Neues – besseres suche.
PS: habe mal so was wie Guerilla -Marketing versucht – wurde nicht verstanden.
Bilder kann ich nach Wunsch liefern.

```html
<!DOCTYPE html>
<html lang="it">
<head>
<meta charset="utf-8">
<title>Verdona – Plakat</title>
<link href="https://fonts.googleapis.com/css2?family=Montserrat:wght@300;400;500;600;700;800&display=swap" rel="stylesheet">
<style>
  :root {
    --backdrop: #e9edf1;
    --paper: #ffffff;
    --forest: #032120;
    --green: #33cc5a;
    --green-deep: #1fa83f;
    --red: #f43a3d;
    --ink: #0b0b0b;
    --white: #ffffff;
  }
  * { box-sizing: border-box; margin: 0; padding: 0; }
  html, body {
    width: 1200px; height: 1177px; overflow: hidden;
    background: var(--backdrop);
    font-family: "Montserrat", Arial, sans-serif;
  }
  .poster {
    position: absolute; left: 199px; top: 20px;
    width: 802px; height: 1137px;
    background: var(--paper);
    box-shadow: 0 4px 18px rgba(0,0,0,.12);
  }
  .photo { position: absolute; }
  .photo-hero {
    left: 0; top: 0; width: 802px; height: 391px;
    background:
      radial-gradient(ellipse 30% 22% at 66% 78%, #5fe0e0 0%, #3cc7cf 60%, transparent 100%),
      linear-gradient(180deg, #cfe6f7 0%, #8fc4ec 26%, #2e8fd0 38%, #4a9bc4 52%, #5e8a4a 70%, #8f9f7e 86%, #c9c4b8 100%);
  }
  .photo-bedroom {
    left: 0; top: 652px; width: 393px; height: 234px;
    background: linear-gradient(160deg, #b9a8c8 0%, #8fb3d0 35%, #e7e4e6 60%, #f3f1ef 80%, #c99b68 100%);
  }
  .photo-bathroom {
    left: 409px; top: 652px; width: 393px; height: 234px;
    background: linear-gradient(170deg, #f1b7b6 0%, #e9a5a6 40%, #8c7f8f 65%, #c39549 85%, #d0a04a 100%);
  }
  .brand-panel {
    position: absolute; left: 0; top: 405px; width: 393px; height: 234px;
    background: var(--forest);
    display: flex; align-items: center; justify-content: center; gap: 12px;
  }
  .brand-dot { width: 20px; height: 20px; border-radius: 50%; background: var(--red); }
  .brand-name {
    color: var(--white); font-weight: 600; font-size: 62px; letter-spacing: 1px;
  }
  .headline-panel {
    position: absolute; left: 409px; top: 405px; width: 393px; height: 234px;
    background: var(--green); color: var(--white);
    padding: 30px 20px 0 27px;
  }
  .headline-main { font-weight: 800; font-size: 36px; line-height: 1; letter-spacing: .3px; }
  .headline-sub { font-weight: 800; font-size: 20.5px; line-height: 1.4; margin-top: 4px; letter-spacing: .3px; }
  .headline-de { font-weight: 400; font-size: 15.5px; line-height: 1.5; margin-top: 14px; }
  .country {
    position: absolute; left: 50px; width: 165px; height: 47px;
    background: var(--red); color: var(--white);
    font-weight: 800; font-size: 17px; letter-spacing: 1px;
    display: flex; align-items: center; padding-left: 28px;
  }
  .country-de { top: 911px; }
  .country-it { top: 968px; letter-spacing: 3.5px; }
  .contact {
    position: absolute; display: flex; align-items: center; gap: 8px;
    font-weight: 700; font-size: 14.5px; color: var(--ink); white-space: nowrap;
  }
  .contact svg { flex: none; }
  .contact .sep { color: var(--green); padding: 0 3px; }
  .contact-mail { left: 238px; top: 922px; }
  .contact-phone-de { left: 476px; top: 922px; }
  .contact-phone-it { left: 238px; top: 979px; }
  .contact-mobile { left: 476px; top: 979px; }
  .web-bar {
    position: absolute; left: 50px; top: 1032px; width: 702px; height: 55px;
    background: var(--forest); color: var(--white);
    display: flex; align-items: center; padding: 0 22px; gap: 9px;
    font-size: 13px; font-weight: 400; white-space: nowrap;
  }
  .web-bar b { font-weight: 700; }
  .web-bar .sep { color: var(--green); font-weight: 700; padding: 0 2px; }
  .social { margin-left: auto; display: flex; align-items: center; gap: 10px; font-size: 15px; }
  .social-square { width: 24px; height: 24px; border-radius: 3px; background: var(--green); }
</style>
</head>
<body>
<main class="poster">
  <div class="photo photo-hero" role="img" aria-label="Villa terrace with kidney-shaped pool, palm trees and a view over the sunlit sea and coastline"></div>

  <section class="brand-panel">
    <span class="brand-dot"></span>
    <span class="brand-name">Verdona</span>
  </section>

  <section class="headline-panel">
    <h1 class="headline-main">VUOI VENDERE</h1>
    <p class="headline-sub">CASA A STRANIERI O<br>AFFITTARLA A TURISTI ?</p>
    <p class="headline-de">wollen Sie Ihre Immobilie an<br>Ausländer verkaufen oder an<br>Touristen vermieten?</p>
  </section>

  <div class="photo photo-bedroom" role="img" aria-label="Bright bedroom with white bed and large windows facing the sea"></div>
  <div class="photo photo-bathroom" role="img" aria-label="Pink bathroom with mosaic tiles, bathtub under a window and a gilded mirror"></div>

  <div class="country country-de">GERMANIA</div>
  <div class="country country-it">ITALIA</div>

  <div class="contact contact-mail">
    <svg width="26" height="18" viewBox="0 0 26 18"><rect x="1" y="1" width="24" height="16" fill="none" stroke="#33cc5a" stroke-width="2"/><path d="M1 1 L13 10 L25 1 M1 17 L10 8 M25 17 L16 8" fill="none" stroke="#33cc5a" stroke-width="2"/></svg>
    <span>info@verdona-beispiel.de</span>
  </div>
  <div class="contact contact-phone-de">
    <svg width="22" height="22" viewBox="0 0 24 24"><path d="M6.6 10.8a15.1 15.1 0 0 0 6.6 6.6l2.2-2.2a1 1 0 0 1 1-.25 11.4 11.4 0 0 0 3.6.57 1 1 0 0 1 1 1V20a1 1 0 0 1-1 1A17 17 0 0 1 3 4a1 1 0 0 1 1-1h3.5a1 1 0 0 1 1 1c0 1.25.2 2.45.57 3.57a1 1 0 0 1-.25 1z" fill="#33cc5a"/></svg>
    <span>+ 49 7412 3810457</span>
  </div>
  <div class="contact contact-phone-it">
    <svg width="22" height="22" viewBox="0 0 24 24"><path d="M6.6 10.8a15.1 15.1 0 0 0 6.6 6.6l2.2-2.2a1 1 0 0 1 1-.25 11.4 11.4 0 0 0 3.6.57 1 1 0 0 1 1 1V20a1 1 0 0 1-1 1A17 17 0 0 1 3 4a1 1 0 0 1 1-1h3.5a1 1 0 0 1 1 1c0 1.25.2 2.45.57 3.57a1 1 0 0 1-.25 1z" fill="#33cc5a"/></svg>
    <span>0571 – 394062</span>
  </div>
  <div class="contact contact-mobile">
    <svg width="14" height="24" viewBox="0 0 14 24"><rect x="1" y="1" width="12" height="22" rx="2" fill="none" stroke="#33cc5a" stroke-width="2"/><circle cx="7" cy="19" r="1.3" fill="#33cc5a"/></svg>
    <span>371 – 2094716<span class="sep">|</span>335- 47 92608</span>
  </div>

  <footer class="web-bar">
    <svg width="22" height="22" viewBox="0 0 24 24"><circle cx="12" cy="12" r="11" fill="#33cc5a"/><g fill="none" stroke="#032120" stroke-width="1.4"><circle cx="12" cy="12" r="7"/><ellipse cx="12" cy="12" rx="3" ry="7"/><path d="M5 12h14M6 8.5h12M6 15.5h12"/></g></svg>
    <span>www.<b>verdonacase-beispiel</b>.com<span class="sep">|</span>www.<b>verdonaaffitti-beispiel</b>.com</span>
    <span class="social"><span class="social-square"></span>verdonacase</span>
  </footer>
</main>
</body>
</html>
```